Tallow Reed Software

We are a software company selling endpoint visibility, access and security technology to enterprise-level IT departments.

Our technology helps organizations gain comprehensive visibility into and control over devices accessing their corporate network so they can quickly identify and address suspicious activity on the network that could lead to potential threats like data breaches.

This technology can cost organizations upwards of $1M - depending on the size of the organization. Our primary clients are Pinnacle 2,000 companies.

We want a professional, polished business card to represent our new brand.

Info fields to include on the card:
Name
Job Title
Office Phone #
Cell Phone #
Email address
Address: 4270 Vestridge Pond Blvd., Ste. 2600, Harrowfield, WI 55812
Website address: www.tallowreedsoftware.example
Tagline: See every device. Secure the network.

Logo files and color specs document are attached. Would like color scheme to coordinate with the logo.

Also looking at stationary/envelope designs in conjunction with the business card designs. Received very few designs that included the stationary.

Software

```html
<!DOCTYPE html>
<html lang="en">
<head>
<meta charset="utf-8">
<title>Tallow Reed Software – Business Card</title>
<link rel="stylesheet" href="https://fonts.googleapis.com/css2?family=Montserrat:wght@500;700&family=Open+Sans:wght@400;600;700&display=swap">
<style>
  :root {
    --stage: #ebe7e3;
    --card: #ffffff;
    --burgundy: #7a2a2e;
    --copper: #c4876c;
    --ink: #1e1e1e;
    --grey: #6b6b6b;
  }
  * { box-sizing: border-box; margin: 0; padding: 0; }
  html, body { width: 1200px; height: 913px; overflow: hidden; }
  body {
    background: var(--stage);
    font-family: "Open Sans", Arial, sans-serif;
    position: relative;
  }
  .card {
    position: absolute;
    width: 520px;
    height: 298px;
    background: var(--card);
    box-shadow: 0 6px 18px rgba(0,0,0,0.12);
    overflow: hidden;
  }
  .card--front { left: 50px; top: 308px; }
  .card--back  { left: 630px; top: 308px; }

  .brand {
    display: flex;
    align-items: center;
    gap: 14px;
  }
  .brand__mark {
    width: 14px; height: 14px;
    border-radius: 50%;
    background: var(--copper);
    flex: none;
  }
  .brand__name {
    font-family: "Montserrat", Arial, sans-serif;
    font-weight: 700;
    color: var(--burgundy);
    text-transform: uppercase;
    letter-spacing: 0.14em;
    line-height: 1;
    white-space: nowrap;
  }

  /* Front */
  .card--front .brand {
    position: absolute; left: 0; right: 0; top: 112px;
    justify-content: center;
  }
  .card--front .brand__name { font-size: 22px; }
  .tagline {
    position: absolute;
    left: 0; right: 0; top: 196px;
    text-align: center;
    font-size: 13px;
    color: var(--grey);
    letter-spacing: 0.02em;
  }

  /* Back */
  .website {
    position: absolute;
    right: 26px; top: 22px;
    font-size: 11px;
    color: var(--grey);
    letter-spacing: 0.03em;
  }
  .card--back .brand { position: absolute; left: 30px; top: 70px; gap: 10px; }
  .card--back .brand__mark { width: 10px; height: 10px; }
  .card--back .brand__name { font-size: 13px; }

  .person { position: absolute; left: 30px; top: 122px; }
  .person__name { font-size: 15px; font-weight: 700; color: var(--ink); }
  .person__title { font-size: 10.5px; font-weight: 600; color: var(--ink); margin-top: 2px; }

  .contact {
    position: absolute; left: 30px; top: 176px;
    font-size: 10.5px; color: var(--ink); line-height: 1.45;
    list-style: none;
  }
  .contact__address { margin-bottom: 6px; }
  .contact__line { display: flex; align-items: center; gap: 7px; }
  .contact__icon { width: 10px; height: 10px; flex: none; fill: var(--burgundy); }

  .edge-band {
    position: absolute; left: 0; right: 0; bottom: 0;
    height: 8px; background: var(--burgundy);
  }
</style>
</head>
<body>

  <section class="card card--front" aria-label="Business card front">
    <div class="brand">
      <span class="brand__mark"></span>
      <span class="brand__name">Tallow Reed Software</span>
    </div>
    <p class="tagline">See every device. Secure the network.</p>
  </section>

  <section class="card card--back" aria-label="Business card back">
    <p class="website">www.tallowreedsoftware.example</p>

    <div class="brand">
      <span class="brand__mark"></span>
      <span class="brand__name">Tallow Reed Software</span>
    </div>

    <div class="person">
      <p class="person__name">Your Long Name</p>
      <p class="person__title">Managing Director</p>
    </div>

    <ul class="contact">
      <li class="contact__address">4270 Vestridge Pond Blvd.<br>Ste. 2600, Harrowfield, WI 55812</li>
      <li class="contact__line">
        <svg class="contact__icon" viewBox="0 0 10 10" aria-hidden="true"><rect x="2.5" y="0.5" width="5" height="9" rx="1"/><rect x="3.5" y="1.8" width="3" height="5.5" fill="#fff"/></svg>
        00.123.123.123
      </li>
      <li class="contact__line">
        <svg class="contact__icon" viewBox="0 0 10 10" aria-hidden="true"><path d="M1 3.5 Q5 0.5 9 3.5 L8 5 L6.5 4.2 L6.5 3.3 Q5 2.8 3.5 3.3 L3.5 4.2 L2 5 Z"/><rect x="2" y="5.5" width="6" height="3.5" rx="0.6"/></svg>
        00.00.00.0000
      </li>
      <li class="contact__line">
        <svg class="contact__icon" viewBox="0 0 10 10" aria-hidden="true"><rect x="0.5" y="2" width="9" height="6.5"/><path d="M0.8 2.3 L5 5.6 L9.2 2.3" fill="none" stroke="#fff" stroke-width="0.9"/></svg>
        yourname@tallowreedsoftware.example
      </li>
    </ul>

    <div class="edge-band"></div>
  </section>

</body>
</html>
```